Jewelers Website

This is for the DESIGN ONLY.
I am a software programmer and will be doing the development.
New website design for
www.lunacrestgems.com.au
Need a fresh new look for an online only jewellery business who produce their jewellery by hand. I would like it designed in a parallax style. Feel free to recommend fonts to use for the site. This is an Australian based company located in NSW so shots of sites in NSW might make nice background images.
http://vornaplex.me/demo/#theme=parallax
To contain the below sections
About Us
Contact Us
Gallery
Testimonials
Diamond Types
The colour scheme is to be Black / White and Silver.
With the Parallax style there will be moving sections and images for added impact.
Target Market(s)
Young Adults mainly engagement jewellery

```html
<!DOCTYPE html>
<html lang="en">
<head>
<meta charset="utf-8">
<title>Lunacrest Gems</title>
<link rel="stylesheet" href="https://fonts.googleapis.com/css2?family=Cinzel:wght@400;700&family=Dancing+Script&family=PT+Serif:ital@0;1&family=Open+Sans:wght@400;600&display=swap">
<style>
:root{
  --black:#0b0b0b;
  --ink:#1a1a1a;
  --panel:#252525;
  --panel-soft:rgba(60,60,60,.82);
  --band:#7a7a7a;
  --silver:#c9c9c9;
  --muted:#9a9a9a;
  --white:#ffffff;
  --accent:#e8553a;
  --globe:#3a7fd5;
  --star:#5bb04a;
  --field:#1e1e1e;
}
*{margin:0;padding:0;box-sizing:border-box}
html,body{width:1200px;height:3871px;overflow:hidden;background:var(--black)}
body{position:relative;font-family:"Open Sans",sans-serif;color:var(--white)}
.abs{position:absolute}
.center{left:0;width:1200px;text-align:center}
.photo{position:absolute}
.heading{font-family:"Cinzel",serif;font-weight:400;letter-spacing:1px}
.script{font-family:"Dancing Script",cursive;font-size:25px;color:var(--silver)}
/* hero */
.hero{top:0;left:0;width:1200px;height:625px;overflow:hidden}
.hero .photo{inset:0;background:linear-gradient(180deg,#3b3a48 0%,#b9704a 18%,#e0854c 24%,#6d6f7a 40%,#4a4f58 70%,#2d3036 100%)}
.hero h1{position:absolute;left:0;width:1200px;text-align:center;font-family:"Cinzel",serif;font-weight:400;line-height:1}
.hero .l1{top:110px;font-size:108px}
.hero .l2{top:255px;font-size:50px}
.hero .l3{top:332px;font-size:70px}
.hero .arrow{position:absolute;top:240px}
.dots{position:absolute;top:556px;left:0;width:1200px;display:flex;justify-content:center;gap:14px}
.dots span{width:13px;height:13px;border-radius:50%;background:var(--white)}
.dots .on{background:var(--accent)}
/* nav */
.nav{top:625px;left:0;width:1200px;height:123px;background:var(--ink)}
.logo{position:absolute;left:129px;top:34px;font-family:"Cinzel",serif;font-size:23px;line-height:26px;color:var(--white)}
.menu{position:absolute;left:420px;top:674px;display:flex;gap:36px;font-family:"Cinzel",serif;font-size:14px;color:var(--silver)}
.menu .current{color:var(--accent)}
/* about */
.about{top:748px;left:0;width:1200px;height:589px}
.about .photo{inset:0;background:linear-gradient(170deg,#9a9a9a 0%,#6a6a6a 35%,#4d4d4d 60%,#8a8a8a 100%)}
.sec-title{position:absolute;left:0;width:1200px;text-align:center;font-family:"Cinzel",serif;font-size:40px}
.sec-sub{position:absolute;left:0;width:1200px;text-align:center}
.feature{position:absolute;top:937px;width:284px;height:317px;background:var(--panel-soft);text-align:center}
.feature .icon{position:absolute;left:108px;top:40px;width:68px;height:68px;border-radius:50%;background:var(--white)}
.feature h3{position:absolute;top:148px;left:0;width:100%;font-family:"PT Serif",serif;font-weight:400;font-size:15px;text-transform:uppercase}
.feature p{position:absolute;top:190px;left:30px;width:224px;font-family:"PT Serif",serif;font-size:12px;line-height:17px;color:var(--muted)}
/* gallery */
.gallery{top:1337px;left:0;width:1200px;height:710px;background:var(--black)}
.tile{position:absolute;width:211px;height:199px;background:var(--panel)}
.tile .photo{left:0;top:0;width:211px;height:147px}
.tile h4{position:absolute;left:10px;top:156px;font-family:"Open Sans",sans-serif;font-size:11px;font-weight:600}
.tile p{position:absolute;left:10px;top:176px;font-size:9px;color:var(--muted)}
.g1{background:radial-gradient(circle at 50% 50%,#f2f2f2,#777)}
.g2{background:linear-gradient(135deg,#fff 40%,#bcbcbc)}
.g3{background:radial-gradient(circle at 50% 55%,#cfcfcf,#111 70%)}
.g4{background:radial-gradient(circle at 50% 60%,#e0e0e0,#2b2b2b 75%)}
.g5{background:linear-gradient(90deg,#d9d9d9,#8d8d8d,#e6e6e6)}
.g6{background:radial-gradient(circle,#222,#000)}
.g7{background:linear-gradient(160deg,#e9eef2,#9fb2be)}
/* testimonials */
.testi{top:2047px;left:0;width:1200px;height:554px}
.testi .photo{inset:0;background:linear-gradient(180deg,#2a2a2a,#4a4a4a 60%,#333)}
.avatar{position:absolute;left:538px;top:2250px;width:124px;height:124px;border-radius:50%;border:4px solid var(--white);background:linear-gradient(#8aa08f,#5c6b60)}
.quote{position:absolute;left:155px;top:2456px;width:890px;text-align:center;font-family:"PT Serif",serif;font-style:italic;font-size:15px;line-height:25px;color:var(--silver)}
.qmark{position:absolute;top:2448px;font-family:"PT Serif",serif;font-size:90px;line-height:1;color:var(--silver)}
/* types */
.types{top:2601px;left:0;width:1200px;height:676px;background:linear-gradient(180deg,#1a1a1a,#0a0a0a)}
.type-card{position:absolute;top:2797px;width:287px;height:428px;background:var(--ink)}
.type-card .photo{left:0;top:0;width:287px;height:206px}
.type-card h3{position:absolute;left:0;top:206px;width:100%;height:42px;line-height:42px;background:var(--band);text-align:center;font-family:"PT Serif",serif;font-weight:400;font-size:15px}
.type-card p{position:absolute;left:25px;top:280px;width:237px;text-align:center;font-family:"PT Serif",serif;font-size:12px;line-height:19px;color:var(--silver)}
.btn{position:absolute;left:68px;top:356px;width:150px;height:44px;background:var(--band);text-align:center;line-height:44px;font-family:"Cinzel",serif;font-size:15px}
/* contact */
.contact{top:3277px;left:0;width:1200px;height:503px}
.contact .photo{inset:0;background:linear-gradient(135deg,#efefef,#d5d5d5 50%,#e4e4e4)}
.field{position:absolute;left:132px;width:510px;background:var(--field);color:var(--silver);font-size:11px;padding:9px 16px}
.submit{position:absolute;left:132px;top:3695px;width:185px;height:49px;background:var(--black);color:var(--white);font-family:"Cinzel",serif;font-size:18px;text-align:center;line-height:49px}
.contact h2{position:absolute;right:130px;top:3318px;font-family:"Cinzel",serif;font-weight:400;font-size:36px;color:var(--black)}
.contact .script{position:absolute;right:130px;top:3374px;width:440px;text-align:right;color:var(--ink);line-height:32px}
.office{position:absolute;top:3473px;height:113px;background:var(--white);color:var(--black);text-align:center;border:2px solid var(--black)}
.office h5{font-family:"Cinzel",serif;font-weight:400;font-size:16px;padding:6px 0 4px;border-bottom:1px solid var(--black)}
.office p{font-size:10px;line-height:14px;padding-top:5px}
/* footer */
.footer{top:3780px;left:0;width:1200px;height:91px;background:var(--black)}
.copy{position:absolute;left:132px;top:38px;font-size:12px;color:var(--silver)}
.social{position:absolute;left:941px;top:30px;display:flex;gap:10px}
.social span{width:29px;height:29px;border-radius:50%;border:2px solid var(--silver)}
</style>
</head>
<body>

<section class="abs hero">
  <div class="photo" role="img" aria-label="Sunset over a wooden jetty with a pelican, New South Wales coast"></div>
  <h1 class="l1">DISCOVER</h1>
  <h1 class="l2">THE POWER OF</h1>
  <h1 class="l3">LUNACREST GEMS</h1>
  <svg class="arrow" style="left:30px" width="40" height="80" viewBox="0 0 40 80"><polyline points="34,4 6,40 34,76" fill="none" stroke="#fff" stroke-width="3"/></svg>
  <svg class="arrow" style="left:1130px" width="40" height="80" viewBox="0 0 40 80"><polyline points="6,4 34,40 6,76" fill="none" stroke="#fff" stroke-width="3"/></svg>
  <div class="dots"><span></span><span class="on"></span><span></span></div>
</section>

<nav class="abs nav">
  <div class="logo">LUNACREST<br>GEMS</div>
</nav>
<div class="menu">
  <span class="current">HOME</span><span>ABOUT US</span><span>GALLERY</span><span>TESTIMONIALS</span><span>DIAMOND TYPES</span><span>CONTACT US</span>
</div>

<section class="abs about">
  <div class="photo" role="img" aria-label="Black and white coastal rocks with a person walking"></div>
</section>
<h2 class="sec-title heading" style="top:798px">ABOUT OUR COMPANY</h2>
<p class="sec-sub script" style="top:855px">Donec eu eros accumsan, feugiat leo non, imperdiet massa, feugiat leo non, imperdiet massa</p>

<div class="feature" style="left:132px">
  <svg class="icon" viewBox="0 0 68 68"><circle cx="34" cy="34" r="34" fill="#fff"/><path d="M34 46 L21 33 A7 7 0 0 1 34 25 A7 7 0 0 1 47 33 Z" fill="var(--accent)"/></svg>
  <h3>We love what we do</h3>
  <p>Class aptent taciti sociosqu ad litora torquent. Nunc turpis nisl, condimentum a quam et, sollicitudin mattis purus.</p>
</div>
<div class="feature" style="left:459px">
  <svg class="icon" viewBox="0 0 68 68"><circle cx="34" cy="34" r="34" fill="#fff"/><circle cx="34" cy="34" r="14" fill="var(--globe)"/></svg>
  <h3>Nationwide service</h3>
  <p>Class aptent taciti sociosqu ad litora torquent. Nunc turpis nisl, condimentum a quam et, sollicitudin mattis purus.</p>
</div>
<div class="feature" style="left:784px">
  <svg class="icon" viewBox="0 0 68 68"><circle cx="34" cy="34" r="34" fill="#fff"/><polygon points="34,18 38.5,29 50,29 41,36 44.5,48 34,41 23.5,48 27,36 18,29 29.5,29" fill="var(--star)"/></svg>
  <h3>We are the best in town</h3>
  <p>Class aptent taciti sociosqu ad litora torquent. Nunc turpis nisl, condimentum a quam et, sollicitudin mattis purus.</p>
</div>

<section class="abs gallery"></section>
<h2 class="sec-title heading" style="top:1390px">OUR GALLERY</h2>
<p class="sec-sub script" style="top:1452px">Donec eu eros accumsan, feugiat leo non, imperdiet massa, feugiat leo non, imperdiet massa</p>

<div class="tile" style="left:132px;top:1525px"><div class="photo g1" role="img" aria-label="Diamond engagement ring"></div><h4>Diamond engagement rings</h4><p>We specialise in the design</p></div>
<div class="tile" style="left:374px;top:1525px"><div class="photo g2" role="img" aria-label="Diamond bangle"></div><h4>Diamond engagement rings</h4><p>We specialise in the design</p></div>
<div class="tile" style="left:614px;top:1525px"><div class="photo g3" role="img" aria-label="Loose diamonds on black"></div><h4>Diamond engagement rings</h4><p>We specialise in the design</p></div>
<div class="tile" style="left:857px;top:1525px"><div class="photo g4" role="img" aria-label="Pile of diamonds"></div><h4>Diamond engagement rings</h4><p>We specialise in the design</p></div>
<div class="tile" style="left:132px;top:1765px"><div class="photo g5" role="img" aria-label="Emerald cut diamond rings"></div><h4>Diamond engagement rings</h4><p>We specialise in the design</p></div>
<div class="tile" style="left:374px;top:1765px"><div class="photo g2" role="img" aria-label="Diamond bangle"></div><h4>Diamond engagement rings</h4><p>We specialise in the design</p></div>
<div class="tile" style="left:614px;top:1765px"><div class="photo g6" role="img" aria-label="Scattered diamonds on black"></div><h4>Diamond engagement rings</h4><p>We specialise in the design</p></div>
<div class="tile" style="left:857px;top:1765px"><div class="photo g7" role="img" aria-label="Diamonds on pale blue"></div><h4>Diamond engagement rings</h4><p>We specialise in the design</p></div>

<section class="abs testi">
  <div class="photo" role="img" aria-label="Dark photo of a couple on a hill"></div>
</section>
<h2 class="sec-title heading" style="top:2128px">STORIES &amp; TESTIMONIALS</h2>
<p class="sec-sub script" style="top:2190px">Donec eu eros accumsan, feugiat leo non, imperdiet massa, feugiat leo non, imperdiet massa</p>
<svg class="abs" style="left:468px;top:2290px" width="24" height="46" viewBox="0 0 24 46"><polyline points="20,3 4,23 20,43" fill="none" stroke="#aaa" stroke-width="3"/></svg>
<div class="avatar" role="img" aria-label="Photo of a happy couple"></div>
<svg class="abs" style="left:694px;top:2290px" width="24" height="46" viewBox="0 0 24 46"><polyline points="4,3 20,23 4,43" fill="none" stroke="#aaa" stroke-width="3"/></svg>
<p class="sec-sub script" style="top:2396px;color:#fff">Mara Lind and Theo</p>
<span class="qmark" style="left:80px">“</span>
<p class="quote">We specialise in the design and creation of one-off pieces of exceptional quality that cannot be found elsewhere. Our team of highly skilled jewellers based in Sydney are committed to making sure that each ring we produce is unique and only the finest materials are used so you can be sure that whatever you order will be truly special. Many Internet jewellery stores stock</p>
<span class="qmark" style="left:1080px">”</span>

<section class="abs types"></section>
<h2 class="sec-title heading" style="top:2670px">DIAMOND TYPES</h2>
<p class="sec-sub script" style="top:2734px">Donec eu eros accumsan, feugiat leo non, imperdiet massa, feugiat leo non, imperdiet massa</p>

<div class="type-card" style="left:132px"><div class="photo g5" role="img" aria-label="Emerald cut engagement rings"></div><h3>ENGAGEMENT RINGS AUSTRALIA</h3><p>pieces that represent fantastic value for money. Furthermore, no matter where you are located in the country, we can supply you</p><div class="btn">READ MORE</div></div>
<div class="type-card" style="left:457px"><div class="photo g1" role="img" aria-label="Diamond heart ring"></div><h3>ENGAGEMENT RINGS AUSTRALIA</h3><p>pieces that represent fantastic value for money. Furthermore, no matter where you are located in the country, we can supply you</p><div class="btn">READ MORE</div></div>
<div class="type-card" style="left:784px"><div class="photo g2" role="img" aria-label="Diamond bangle"></div><h3>ENGAGEMENT RINGS AUSTRALIA</h3><p>pieces that represent fantastic value for money. Furthermore, no matter where you are located in the country, we can supply you</p><div class="btn">READ MORE</div></div>

<section class="abs contact">
  <div class="photo" role="img" aria-label="Light grey street map"></div>
</section>
<div class="field" style="top:3328px;height:39px">Name:</div>
<div class="field" style="top:3385px;height:39px">Email:</div>
<div class="field" style="top:3442px;height:41px">Phone:</div>
<div class="field" style="top:3499px;height:165px">Message:</div>
<div class="submit">SUBMITT</div>
<h2 class="heading" style="position:absolute;left:790px;top:3312px;font-size:36px;color:var(--black)">CONTACT US</h2>
<p class="script" style="position:absolute;left:640px;top:3370px;width:430px;text-align:right;color:var(--ink);line-height:32px">Donec eu eros accumsan, feugiat leo non, imperdiet massa, feugiat leo non, imperdiet massa</p>
<div class="office" style="left:820px;width:101px"><h5>SYDNEY</h5><p>Brookvale NSW<br>2100, Australia<br>Phone +61 (0)<br>2 9000 4812</p></div>
<div class="office" style="left:941px;width:119px"><h5>GERMANY</h5><p>Germany 50210<br>Kaltenbach<br>Phone +49(0)<br>2100 5550417</p></div>
<svg class="abs" style="left:1105px;top:3512px" width="26" height="38" viewBox="0 0 26 38"><path d="M13 37 C4 24 1 19 1 13 A12 12 0 0 1 25 13 C25 19 22 24 13 37 Z" fill="#111"/><circle cx="13" cy="13" r="4.5" fill="#fff"/></svg>

<footer class="abs footer">
  <p class="copy">© 2014 lunacrestgems all rights are reserved</p>
  <div class="social"><span></span><span></span><span></span><span></span></div>
</footer>

</body>
</html>
```